Whitcombe Business Card Design

The name of the business is Dario Whitcombe, CPA LLC
The service that we offer is Accounting, Tax & Consulting Services. I need it to have the following items:
Dario Whitcombe, Principal
Phone Number
Email Address
Physical Address

I have attached the company logo, one in black and one in white. Please provide a design in black background and the other in white background. Please include "Accounting, Tax & Consulting Services". I want the business card to be clean and very professional.

```html
<!DOCTYPE html>
<html lang="en">
<head>
<meta charset="utf-8">
<title>Whitcombe Business Card</title>
<link href="https://fonts.googleapis.com/css2?family=Montserrat:wght@500;600&family=Arimo:ital,wght@0,400;1,400&display=swap" rel="stylesheet">
<style>
  :root {
    --stage: #1c1c1d;
    --card: #333334;
    --card-pattern: #2c2c2d;
    --edge-red: #a3161c;
    --brand-red: #b3161d;
    --white: #ffffff;
    --muted: #9a9a9c;
  }
  * { box-sizing: border-box; margin: 0; padding: 0; }
  html, body {
    width: 1200px; height: 900px; overflow: hidden;
    background: var(--stage);
  }
  .canvas {
    width: 1200px; height: 900px;
    display: flex; flex-direction: column;
    align-items: center; justify-content: center; gap: 40px;
  }
  .card {
    position: relative;
    width: 630px; height: 360px;
    border-radius: 22px;
    background: var(--card);
    border-bottom: 5px solid var(--edge-red);
    overflow: hidden;
    font-family: "Arimo", Arial, sans-serif;
    color: var(--white);
  }

  /* Front */
  .brand {
    position: absolute; left: 48px; top: 48px;
    display: flex; align-items: center; gap: 12px;
  }
  .brand-square {
    width: 22px; height: 22px; background: var(--white);
  }
  .brand-name {
    font-family: "Montserrat", Arial, sans-serif;
    font-weight: 600; font-size: 21px; color: var(--white);
  }
  .brand-tagline {
    position: absolute; left: 48px; top: 84px;
    font-family: "Montserrat", Arial, sans-serif;
    font-weight: 500; font-size: 11.5px; letter-spacing: 3.4px;
    color: var(--muted); text-transform: uppercase;
  }
  .contact {
    position: absolute; left: 48px; top: 140px;
    list-style: none; font-size: 16px; line-height: 26px;
  }
  .contact li { display: flex; align-items: center; gap: 9px; }
  .contact .address { padding-left: 21px; }
  .contact svg { width: 12px; height: 12px; flex: none; fill: var(--brand-red); }
  .person {
    position: absolute; right: 48px; top: 210px; text-align: right;
  }
  .person-name {
    font-size: 30px; color: var(--brand-red); text-transform: uppercase;
    letter-spacing: 0.5px;
  }
  .person-role {
    margin-top: 6px; font-size: 17px; font-style: italic;
  }

  /* Back */
  .card--back { background: var(--card-pattern); }
  .pattern-field {
    position: absolute; inset: 0;
    background: linear-gradient(135deg, #2a2a2b 0%, #343435 55%, #3d3d3e 100%);
  }
  .services {
    position: absolute; right: 48px; bottom: 40px;
    display: flex; align-items: center; gap: 18px;
  }
  .services-line { font-size: 17px; font-style: italic; }
  .services-brand {
    display: flex; align-items: center; gap: 10px;
  }
  .services-brand .brand-square { width: 18px; height: 18px; }
  .services-brand .brand-name { font-size: 16px; }
</style>
</head>
<body>
<main class="canvas">

  <section class="card card--front" aria-label="Business card front">
    <div class="brand">
      <span class="brand-square"></span>
      <span class="brand-name">Dario Whitcombe, CPA LLC</span>
    </div>
    <p class="brand-tagline">Certified Public Accountant</p>

    <ul class="contact">
      <li class="address">1480 N Halden Avenue</li>
      <li class="address">Brierly County 6042</li>
      <li>
        <svg viewBox="0 0 12 12" aria-hidden="true"><path d="M2.5 0.8 L4.6 0.8 L5.2 3.4 L3.9 4.5 Q5 6.9 7.5 8.1 L8.6 6.8 L11.2 7.4 L11.2 9.5 Q11.2 11.2 9.5 11.2 Q0.8 10.4 0.8 2.5 Q0.8 0.8 2.5 0.8 Z"/></svg>
        415-362-0918
      </li>
      <li>
        <svg viewBox="0 0 12 12" aria-hidden="true"><path d="M0.5 2 H11.5 V10 H0.5 Z M1.3 2.8 L6 6.4 L10.7 2.8 Z" fill-rule="evenodd"/></svg>
        info@whitcombecpa.com
      </li>
      <li>
        <svg viewBox="0 0 12 12" aria-hidden="true"><circle cx="6" cy="6" r="5.4"/><path d="M0.6 6 H11.4 M6 0.6 V11.4" stroke="#333334" stroke-width="0.9"/></svg>
        www.whitcombecpa.com
      </li>
    </ul>

    <div class="person">
      <p class="person-name">Dario Whitcombe</p>
      <p class="person-role">Principal</p>
    </div>
  </section>

  <section class="card card--back" aria-label="Business card back">
    <div class="pattern-field" role="img" aria-label="Tonal embossed repeat pattern background"></div>
    <div class="services">
      <p class="services-line">Accounting, Tax &amp; Consulting Services</p>
      <div class="services-brand">
        <span class="brand-square"></span>
        <span class="brand-name">Dario Whitcombe</span>
      </div>
    </div>
  </section>

</main>
</body>
</html>
```